Whitcombe Business Card Design

The name of the business is Dario Whitcombe, CPA LLC
The service that we offer is Accounting, Tax & Consulting Services. I need it to have the following items:
Dario Whitcombe, Principal
Phone Number
Email Address
Physical Address

I have attached the company logo, one in black and one in white. Please provide a design in black background and the other in white background. Please include "Accounting, Tax & Consulting Services". I want the business card to be clean and very professional.

```html
<!DOCTYPE html>
<html lang="en">
<head>
<meta charset="utf-8">
<title>Dario Whitcombe, CPA LLC — Business Cards</title>
<link href="https://fonts.googleapis.com/css2?family=Montserrat:wght@600&family=Arimo:wght@400;700&display=swap" rel="stylesheet">
<style>
  :root {
    --backdrop: #c9c8c5;
    --card: #ffffff;
    --brand-red: #a3161d;
    --ink: #2b2b2d;
    --muted: #8e8e90;
    --rule: #bdbdbd;
  }
  * { box-sizing: border-box; margin: 0; padding: 0; }
  html, body { width: 1200px; height: 801px; overflow: hidden; }
  body {
    background: var(--backdrop);
    font-family: "Arimo", Arial, sans-serif;
    color: var(--ink);
    display: flex;
    align-items: center;
    justify-content: center;
    gap: 60px;
  }
  .card {
    position: relative;
    width: 525px;
    height: 300px;
    background: var(--card);
    border-bottom: 5px solid var(--brand-red);
    box-shadow: 0 10px 24px rgba(0,0,0,0.18);
  }
  .wordmark {
    font-family: "Montserrat", Arial, sans-serif;
    font-weight: 600;
    color: var(--ink);
    letter-spacing: 0.3px;
    display: flex;
    align-items: center;
    gap: 8px;
    white-space: nowrap;
  }
  .wordmark-square {
    width: 11px; height: 11px;
    background: var(--brand-red);
    flex: none;
  }

  /* Front */
  .card-front .wordmark {
    position: absolute;
    left: 24px; top: 158px;
    width: 230px;
    font-size: 14px;
  }
  .divider {
    position: absolute;
    left: 268px; top: 62px;
    width: 1px; height: 150px;
    background: linear-gradient(var(--rule) 0 28%, var(--brand-red) 28% 72%, var(--rule) 72%);
  }
  .contact {
    position: absolute;
    left: 290px; top: 52px;
    width: 215px;
    font-size: 11.5px;
    line-height: 1.45;
  }
  .contact-name {
    font-family: "Montserrat", Arial, sans-serif;
    font-weight: 600;
    font-size: 18px;
    color: var(--brand-red);
    letter-spacing: 0.2px;
    line-height: 1.1;
    white-space: nowrap;
  }
  .contact-title { margin-bottom: 8px; }
  .contact-address { margin-bottom: 6px; }
  .contact-row { display: flex; align-items: center; gap: 6px; white-space: nowrap; }
  .contact-row svg { width: 10px; height: 10px; flex: none; }
  .services {
    position: absolute;
    left: 0; right: 26px; bottom: 34px;
    text-align: right;
    font-size: 12.5px;
    letter-spacing: 0.2px;
  }

  /* Back */
  .card-back .wordmark {
    position: absolute;
    left: 0; right: 0; top: 0; bottom: 0;
    justify-content: center;
    font-size: 24px;
    gap: 10px;
  }
  .card-back .wordmark-square { width: 16px; height: 16px; }
</style>
</head>
<body>
  <section class="card card-front" aria-label="Card front">
    <div class="wordmark"><span class="wordmark-square"></span>Dario Whitcombe, CPA LLC</div>
    <div class="divider"></div>
    <div class="contact">
      <p class="contact-name">DARIO WHITCOMBE</p>
      <p class="contact-title">Principal</p>
      <p class="contact-address">418 N Carver Avenue<br>Halden County 6042</p>
      <p class="contact-row">
        <svg viewBox="0 0 10 10"><circle cx="5" cy="5" r="5" fill="#a3161d"/><path d="M3 2.6c.4-.3.8 0 1 .5l.2.5c.1.3-.2.5-.3.7.3.7.8 1.2 1.4 1.5.2-.1.4-.4.7-.3l.5.2c.5.2.7.6.4 1-.6.8-1.8.5-2.8-.4C3.2 5.4 2.2 3.4 3 2.6z" fill="#fff"/></svg>
        555-302-1187
      </p>
      <p class="contact-row">
        <svg viewBox="0 0 10 10"><circle cx="5" cy="5" r="5" fill="#a3161d"/><rect x="2.4" y="3.2" width="5.2" height="3.6" fill="#fff"/><path d="M2.4 3.2 5 5.3l2.6-2.1" fill="none" stroke="#a3161d" stroke-width=".6"/></svg>
        office@whitcombecpa-mail.com
      </p>
      <p class="contact-row">
        <svg viewBox="0 0 10 10"><circle cx="5" cy="5" r="5" fill="#a3161d"/><circle cx="5" cy="5" r="2.6" fill="none" stroke="#fff" stroke-width=".7"/><path d="M2.4 5h5.2M5 2.4c-1.2 1.5-1.2 3.7 0 5.2M5 2.4c1.2 1.5 1.2 3.7 0 5.2" fill="none" stroke="#fff" stroke-width=".6"/></svg>
        www.whitcombecpa-office.com
      </p>
    </div>
    <p class="services">Accounting, Tax &amp; Consulting Services</p>
  </section>

  <section class="card card-back" aria-label="Card back">
    <div class="wordmark"><span class="wordmark-square"></span>Dario Whitcombe, CPA LLC</div>
  </section>
</body>
</html>
```